Modern Business Card

Modern professional business card with more than just logo and demographic info. Something memorable.

We are a trendy/modern chiropractic group with an emphasis on neurology, hence the minimalist-type brain logo. We want to convey that modern and technical aspect with professionalism and the elite nature of our practice environment.

```html
<!DOCTYPE html>
<html lang="en">
<head>
<meta charset="utf-8">
<title>Clarity Spine – Business Card</title>
<link rel="stylesheet" href="https://fonts.googleapis.com/css2?family=Open+Sans:wght@400;600;700&display=swap">
<style>
  :root {
    --brand-blue: #4a80c6;
    --brand-blue-dark: #3f72b6;
    --swoosh-grey: #5a5c60;
    --ink: #3a3a3a;
    --paper: #ffffff;
    --backdrop: #e4e4e2;
  }
  * { box-sizing: border-box; margin: 0; padding: 0; }
  html, body { width: 1200px; height: 801px; overflow: hidden; }
  body {
    background: var(--backdrop);
    font-family: "Open Sans", Arial, sans-serif;
    position: relative;
  }
  .card {
    position: absolute;
    width: 520px;
    height: 297px;
    top: 252px;
    overflow: hidden;
    box-shadow: 0 6px 18px rgba(0,0,0,0.18);
  }
  .card--front { left: 50px; background: var(--paper); }
  .card--back { left: 630px; background: var(--brand-blue); }
  .card__shape { position: absolute; inset: 0; }

  .brand {
    position: absolute;
    left: 26px;
    top: 150px;
    display: flex;
    align-items: center;
    gap: 9px;
  }
  .brand__dot {
    width: 22px; height: 22px;
    border-radius: 50%;
    background: var(--brand-blue);
  }
  .brand__name {
    font-weight: 700;
    font-size: 21px;
    letter-spacing: 0.5px;
    color: var(--ink);
    text-transform: uppercase;
    white-space: nowrap;
  }

  .contact {
    position: absolute;
    left: 248px;
    top: 18px;
    padding-left: 11px;
    border-left: 1.5px solid var(--brand-blue);
    color: var(--ink);
    font-size: 11px;
    line-height: 15px;
    white-space: nowrap;
  }
  .contact__name {
    color: var(--brand-blue);
    font-weight: 700;
    font-size: 15px;
    line-height: 19px;
    letter-spacing: 0.3px;
  }
  .contact__title { margin-bottom: 6px; }
  .contact__address { margin-bottom: 6px; }
  .contact__line { display: flex; align-items: center; gap: 5px; }
  .contact__icon { width: 10px; height: 10px; flex: none; }

  .pattern-field { position: absolute; inset: 0; background: linear-gradient(135deg, var(--brand-blue) 0%, var(--brand-blue-dark) 100%); }
  .back-brand {
    position: absolute;
    right: 48px;
    top: 126px;
    display: flex;
    align-items: center;
    gap: 8px;
  }
  .back-brand__dot { width: 20px; height: 20px; border-radius: 50%; background: var(--paper); }
  .back-brand__name {
    color: var(--paper);
    font-weight: 700;
    font-size: 18px;
    letter-spacing: 1px;
    text-transform: uppercase;
  }
</style>
</head>
<body>
  <section class="card card--front" aria-label="Business card front">
    <svg class="card__shape" viewBox="0 0 520 297" aria-hidden="true">
      <path d="M0 297 L0 272 Q380 250 520 40 L520 297 Z" fill="var(--brand-blue)"/>
      <path d="M285 206 Q435 147 512 32" fill="none" stroke="var(--swoosh-grey)" stroke-width="5" stroke-linecap="round"/>
    </svg>

    <div class="brand">
      <span class="brand__dot"></span>
      <span class="brand__name">Clarity Spine</span>
    </div>

    <div class="contact">
      <div class="contact__name">DAN WHITFORD</div>
      <div class="contact__title">President</div>
      <div class="contact__address">1840 Harbor Crest Lane<br>Seabrook CA 92600</div>
      <div class="contact__line">
        <svg class="contact__icon" viewBox="0 0 12 12"><path d="M3 1 L5 3.5 L3.8 4.8 Q5 7.2 7.2 8.2 L8.5 7 L11 9 L9.6 10.8 Q4 10 1.2 2.4 Z" fill="var(--brand-blue)"/></svg>
        <span>555-014-2270</span>
      </div>
      <div class="contact__line">
        <svg class="contact__icon" viewBox="0 0 12 12"><rect x="1" y="3" width="10" height="7" rx="1" fill="var(--brand-blue)"/><path d="M1.5 3.5 L6 7 L10.5 3.5" fill="none" stroke="#fff" stroke-width="1"/></svg>
        <span>dan@clarityspine.com</span>
      </div>
      <div class="contact__line">
        <svg class="contact__icon" viewBox="0 0 12 12"><circle cx="6" cy="6" r="5" fill="var(--brand-blue)"/><path d="M1 6 H11 M6 1 Q3 6 6 11 M6 1 Q9 6 6 11" fill="none" stroke="#fff" stroke-width="0.8"/></svg>
        <span>www.clarityspine.com</span>
      </div>
    </div>
  </section>

  <section class="card card--back" aria-label="Business card back">
    <div class="pattern-field" role="img" aria-label="Subtle repeating brand pattern in light blue tones"></div>
    <div class="back-brand">
      <span class="back-brand__dot"></span>
      <span class="back-brand__name">Clarity Spine</span>
    </div>
  </section>
</body>
</html>
```